The design should look similar to the uploaded example to accommodate the information needed for a business card template. I would like to see the colors orange and charcoal grey incorporated along with the logo.The following should be on the back of the card SPECIALIZING IN NEW AND USED TIRES & WHEELS FOR:- Loaders- Skid Steers- Telehandlers- Boom Lifts- Forklifs and moreELIMINATING DOWNTIMEWheel Exchange Program for New & Used Foam Filled and Solid Rubber TiresSPECIALTY SERVICES- Foam Filling Tires- Largest Tire Press in SE- ONSITE Forklift Tire Press- Boom Truck Services - Rubber Tracks

Target Market(s)

New and Existing Customers

Industry/Entity Type

Business

Contact Information for Business Card

NAMEHEAVY DUTY TIRE, LLC8470 Belvedere RoadWest Palm Beach, FL 33411P: 844-HD-TIRESF: 561-431-6469C:E: W: WWW.GRANITERIMSUPPLY-EXAMPLE.COM

Font styles to use
Sans Serif

Colors
f37122
333333

Requirements
Must have
• The logo and the information indicated for the backside of the card
Nice to have
• Keep the orange and charcoal grey colors

```html
<!DOCTYPE html>
<html lang="en">
<head>
<meta charset="utf-8">
<title>Granite Rim Supply, LLC — Business Card</title>
<link href="https://fonts.googleapis.com/css2?family=Roboto:wght@400;500;700;900&display=swap" rel="stylesheet">
<style>
  :root {
    --orange: #f37122;
    --charcoal: #333333;
    --slate: #3e4b57;
    --slate-dark: #34404b;
    --paper: #ffffff;
    --ink-soft: #4a4f55;
    --back-text: #dfe4e8;
    --stage: #e9e9e9;
  }
  * { box-sizing: border-box; margin: 0; padding: 0; }
  html, body {
    width: 1200px; height: 950px; overflow: hidden;
    background: var(--stage);
    font-family: "Roboto", Arial, sans-serif;
  }
  .card {
    position: absolute; left: 220px;
    width: 760px; height: 434px;
    border-radius: 4px;
    box-shadow: 0 6px 18px rgba(0,0,0,.18);
    overflow: hidden;
  }

  /* ---------- Back of card ---------- */
  .card-back {
    top: 24px;
    background: linear-gradient(120deg, var(--slate) 0%, var(--slate-dark) 100%);
    color: var(--back-text);
    padding: 40px 48px 36px;
    display: flex; flex-direction: column; justify-content: space-between;
  }
  .brand { display: flex; align-items: center; gap: 16px; }
  .brand-dot { border-radius: 50%; background: var(--orange); flex: none; }
  .brand-name { font-weight: 900; line-height: 1.05; letter-spacing: .5px; }
  .card-back .brand { justify-content: center; }
  .card-back .brand-dot { width: 70px; height: 70px; }
  .card-back .brand-name { color: #ffffff; font-size: 30px; }
  .service-block { }
  .service-heading {
    color: #ffffff; font-weight: 700; font-size: 19px;
    text-transform: uppercase; letter-spacing: .4px; margin-bottom: 5px;
  }
  .service-list { list-style: none; font-size: 16.5px; line-height: 1.5; }
  .service-list span { white-space: nowrap; }
  .bullet { color: var(--orange); margin: 0 7px; }

  /* ---------- Front of card ---------- */
  .card-front { top: 490px; background: linear-gradient(110deg, #ffffff 55%, #f1f1f1 100%); }
  .edge-band { position: absolute; left: 0; top: 0; width: 22px; height: 100%; background: var(--slate); }
  .edge-accent { position: absolute; left: 22px; top: 0; width: 18px; height: 112px; background: var(--orange); }
  .card-front .brand { position: absolute; left: 66px; top: 30px; }
  .card-front .brand-dot { width: 80px; height: 80px; }
  .card-front .brand-name { color: var(--charcoal); font-size: 32px; }
  .contact {
    position: absolute; left: 80px; top: 150px;
    list-style: none; color: var(--ink-soft); font-size: 19px; line-height: 29px;
  }
  .contact li { display: flex; align-items: center; gap: 12px; }
  .contact .address { padding-left: 30px; }
  .contact svg { width: 18px; height: 18px; flex: none; fill: var(--slate); }
  .person { position: absolute; right: 66px; bottom: 46px; text-align: left; }
  .person-name { color: var(--slate); font-size: 27px; font-weight: 500; letter-spacing: .5px; }
  .person-title { color: var(--orange); font-size: 17px; letter-spacing: 1px; margin-top: 2px; }
</style>
</head>
<body>

<section class="card card-back">
  <div class="brand">
    <span class="brand-dot"></span>
    <span class="brand-name">GRANITE RIM<br>SUPPLY LLC</span>
  </div>

  <div class="service-block">
    <h2 class="service-heading">Specializing in new and used tires &amp; wheels for</h2>
    <ul class="service-list">
      <li><span>Loaders</span><span class="bullet">•</span><span>Skid Steers</span><span class="bullet">•</span><span>Telehandlers</span><span class="bullet">•</span><span>Boom Lifts</span><span class="bullet">•</span><span>Forklifts and more</span></li>
    </ul>
  </div>

  <div class="service-block">
    <h2 class="service-heading">Eliminating downtime</h2>
    <ul class="service-list">
      <li>Wheel Exchange Program for New &amp; Used Foam Filled and Solid Rubber Tires</li>
    </ul>
  </div>

  <div class="service-block">
    <h2 class="service-heading">Specialty services</h2>
    <ul class="service-list">
      <li><span>Foam Filling Tires</span><span class="bullet">•</span><span>Largest Tire Press in SE</span><span class="bullet">•</span><span>ONSITE Forklift Tire Press</span></li>
      <li><span>Boom Truck Services</span><span class="bullet">•</span><span>Rubber Tracks</span></li>
    </ul>
  </div>
</section>

<section class="card card-front">
  <div class="edge-band"></div>
  <div class="edge-accent"></div>

  <div class="brand">
    <span class="brand-dot"></span>
    <span class="brand-name">GRANITE RIM<br>SUPPLY LLC</span>
  </div>

  <ul class="contact">
    <li class="address">5126 Marston Lane</li>
    <li class="address">Lake Harlow, FL 33490</li>
    <li>
      <svg viewBox="0 0 16 16" aria-hidden="true"><path d="M3 1h3l1.5 4-2 1.2a9 9 0 0 0 4.3 4.3L11 8.5l4 1.5v3a2 2 0 0 1-2 2A12 12 0 0 1 1 3a2 2 0 0 1 2-2z"/></svg>
      844-GR-WHEEL
    </li>
    <li>
      <svg viewBox="0 0 16 16" aria-hidden="true"><path d="M4.5 0h7A1.5 1.5 0 0 1 13 1.5v13a1.5 1.5 0 0 1-1.5 1.5h-7A1.5 1.5 0 0 1 3 14.5v-13A1.5 1.5 0 0 1 4.5 0zM5 2v10h6V2zm3 11a1 1 0 1 0 0 2 1 1 0 0 0 0-2z"/></svg>
      836 555 0172
    </li>
    <li>
      <svg viewBox="0 0 16 16" aria-hidden="true"><path d="M4 0h8v5H4zM1 6h14v7h-3v3H4v-3H1zm4 5v4h6v-4z"/></svg>
      561-278-9053
    </li>
    <li>
      <svg viewBox="0 0 16 16" aria-hidden="true"><path d="M0 3h16v1L8 9 0 4zM0 5.5l8 5 8-5V13H0z"/></svg>
      name@graniterimsupply-example.com
    </li>
    <li>
      <svg viewBox="0 0 16 16" aria-hidden="true"><circle cx="8" cy="8" r="7.5"/><path d="M8 .5v15M.5 8h15M3 3.5q5 3 10 0M3 12.5q5-3 10 0" stroke="#fff" stroke-width="1" fill="none"/></svg>
      www.graniterimsupply-example.com
    </li>
  </ul>

  <div class="person">
    <div class="person-name">MARK ELLISON</div>
    <div class="person-title">PRESIDENT</div>
  </div>
</section>

</body>
</html>
```